Ecological Cosmetics (w/ Social Impact) Website

Dr. Wendelin Marovitz Naturprodukte KELVORA®, a small family-run ecological cosmetics “start-up” business (has been around since the mid 90s but only now beginning professionalize management), wishes to redesign its web presence, as part of a comprehensive “facelift” that will also encompass at a later stage its corporate identity (e.g. logo…).
We would like to prepare a new trilingual (later 3 additional languages will be added) website (www.kelvora7.at) that is symbiotic with web 2.0 enabled interwoven with a blog, news section, social networks integrated (e.g. preference/like buttons, Facebook), changing images and announcements appearing on first page, online payment services, mobile internet compatibility (e.g. iOS, Android, BlackBerry… thus no use of Flash, no need for a specific app), etc. and all the other significant trends in the e-commerce realm. The website should be easily and quickly accessible, fun to navigate, allow us to update it simply (through a content manager) and so “sexy” that people will want to return to the web, inform themselves of events and news, and hopefully also try our products.
Our company is based in Austria and specializes in the production of organic cosmetics in the mid-upper pricing range. We pride ourselves in offering natural cosmetics (the meaning of “natural” is relative and each person may have a different definition), with no petrochemical preservatives. Some of our products, such as the mineral salts and black mud powder from the Dead Sea cannot be obtained more naturally, unless you actually visit the area, thus retain all their properties. Our products are not medicine but the basic Dead Sea ingredients are used by spas and clinics in the area to treat many different skin, joint and bone affections. Our male and female customers (no distinction made will be made on our new website), primarily as of the ages of 25 to 65, buy KELVORA® because they:
• Care about the exterior and interior well-being
• Wish to look well cared, preserve their skin’s flexibility, natural splendor & properties
• Prefer natural skin care
• Nourish their skin with vital minerals/trace elements, protecting/treating their skin with natural ingredients
• Willing to pay more than average for natural cosmetics, looking for quality,
• Don’t mind spending about 15 minutes per week preparing a mud mask with some hot water.
• Bathe in water enriched with mineral salts
• Know or are surprised to find out that Dead Sea mud is one of the few, if not the only, naturally astringent (tenses the skin) muds in the world
• Help alleviate skin conditions (e.g. psoriasis, dermatitis, acne, eczema, pustules, oily skin ...), joint (e.g. rheumatism, arthritis ...) and cardiovascular disease.
Amongst the minerals in many of our products (particularly salt, mud), are sulfur and zinc, two naturally disinfecting and healing minerals, thus their common use in many dermatological drugs. Both salt and mud powder are completely natural, and without chemicals additives, quite important when dealing with sensitive or problematic skin, which reacts allergically to certain types of substances. The KELVORA line blends in both ingredients, enriching them with the highest-quality vitamins, essential oils and exceptional plant oils. Many of the competitors creams today use common ingredients such as petrolatum, paraffin (paraffinum liquidum), mineral oil, among others, which are derived from oil, are cheap ingredients (higher margins!) and clog pores!
To underline that this is not a chimera, there are quite a few researchers/scientists/doctors who have written articles about the benefits of the Dead Sea and its naturally occurring substances. Below are some links to abstracts of research papers, which are helpful in understanding the therapeutic potential of the black mud powder and mineral salt:
http://onlinelibrary.wiley.com/doi/10.1111/j.1365-4362.1995.tb03599.x/abstract
http://onlinelibrary.wiley.com/doi/10.1111/j.1365-4632.2005.02079.x/full
http://onlinelibrary.wiley.com/doi/10.1046/j.1365-4362.1997.00204.x/abstract
http://ard.bmj.com/content/49/2/99.short
http://www.springerlink.com/content/pv46n2p1m9p3k131/
http://onlinelibrary.wiley.com/doi/10.1111/j.1365-4632.2005.02621.x/full
http://journals.lww.com/jclinrheum/Abstract/2002/08000/Therapy_With_Mud_Compresses_for_Knee.3.aspx
http://onlinelibrary.wiley.com/doi/10.1111/j.1468-3083.1997.tb00509.x/abstract
http://onlinelibrary.wiley.com/doi/10.1046/j.1529-8019.2003.01622.x/full
http://onlinelibrary.wiley.com/doi/10.1046/j.1365-4362.1999.00583.x/full
The following links lead you to KELVORA® product data, mineral characteristics and a video of how to prepare a facial mud mask:
http://www.kelvora7.at/descargaanalisis.htm
http://www.kelvora7.at/estudio.htm
http://www.clipverse.example/watch?v=Qm4TzLp8WxR
We would like to convey, through our striking and attractive new graphic design, our values to potential clients: quality, 100% natural product, effectiveness, seriousness, confidence, respect for the environment, people, animals (the products are not tested on animals), all of which has a price (they are not cheap!). To put our money where our mouth is and contribute to transforming our planet into a better place, we are discussing with NGOs donating a percentage of certain product sales to support their causes.
Our web currently is available in 3 languages: German, Spanish and English, however, we plan to expand it by another 2 to 3 languages (Portuguese, Russian, Chinese). We are looking for a graphic design that will communicate our values and captivate people's attention, thereby helping us increase sales, projecting a solid and elegant image of reliability, effectiveness, simplicity and trust. Although we are not, and do not wish to, market our products as medicine, we do want to express, through our new graphic design, the fact that these products can be used to treat all types of skin, mitigate certain skin affections (e.g. psoriasis, dermatitis, acne, eczema, sensitive skin), and, depending on each organism’s reaction, different ailments (e.g. arthritis, rheumatism), although they won’t cure them (they can alleviate!).
To get an idea of our company, I invite you to explore our website, www.kelvora7.at, and see photos of our products. Attached please find some photos of our products, including the newly designed black mud powder box. We would like to create a unified corporate image. At this point we know that some, if not all, packages do not convey quality nor our values – this is something we wish to gradually change as each products’ graphic design and packaging gets renewed, consistent with the new brand image. This is work-in-progress and will be addressed as the company grows and has the financial capacity to invest in new design and packaging. We are advancing step by step.
Content-wise, we would provide you with product photos, and the texts to be inserted, but would like to complement these with other photos (e.g. from photobanks that include images of the Dead Sea, beaches, plants, nature…). The design should quickly associate the Internet user/visitor of our website with our values and the idea of quality products. A content manager will be used to update and modify our product portfolio.
Although some people will find us by typing into their web browser the address of our website, many will use search engines to locate us on the WWW. For this purpose, it would also be important that kelvora7.at’s different webpages can be referenced, searched for keywords and allow analysis of webtraffic (e.g. Google Analytics…).
Two colors are being used in our packages, green Pantone No. 326 and blue Pantone No. 072. We are completely flexible in terms of colors.
We hope you find the project interesting. Any questions, please do not hesitate to contact us. Thank you very much for your time, recommendations and proposals. Ideally we can close this project in about 14 days.
Information to be considered and/or included in the design:
• The web will feature an e-commerce shop, whose design should also be included in your creative proposal.
• Cosmetics tend to be divided along the lines of skin types, yet as the KELVORA line is still quite small, we have decided to divide it along treatment areas: hair, face, body. Each product is indicated for a particular skin type.
• Keyword Search box for the entire website
The current web is slow, all in Flash, difficult to navigate, has too many intermediate stages, does not offer a keyword search function, nor incorporate any web 2.0 features. Furthermore, it is more difficult to find and index in search engines as none of the pages have specific web addresses. In terms of intermediate pages, these should be eliminated shortening the time the user needs to obtain the desired information (e.g. the landing page where you choose sex & language, followed by drop of water being filled up), such that the visitor is directly lead to the main page (equal to the landing page). At first glance, the blue background and the drop of water filling up may lead the visitor to believe we are dedicated to something with water, perhaps even plumbing or purification services – such an impression must be avoided. Perhaps one of the ways to analyze all the aspects to be incorporated is an evaluation of our current web’s weaknesses and prepare a design where those are all addressed.
Target Market(s)
Male & female customers, approx. age 18-65, who care about their exterior and interior well being, “worried” about their skin, willing to pay more tha
Industry/Entity Type
Graphic Design
Requirements
Must have
- • The web will also feature a blog and an e-commerce shop, whose designs should also be included in your creative proposal.
• Address current and future languages
Content-wise, we will product photos, and the texts to be inserted, but would like to complement these with other photos (e.g. from photobanks that include images of the Dead Sea, beaches, plants, nature…). The design should quickly associate the Internet user/visitor of our website with our values and the idea of quality products. A content manager will be used to update and modify our product portfolio, as well as effects announcements on the landing page.

```html
<!DOCTYPE html>
<html lang="en">
<head>
<meta charset="utf-8">
<title>KELVORA® Naturprodukte</title>
<link href="https://fonts.googleapis.com/css2?family=Oswald:wght@300;400;500&family=Open+Sans:wght@400;600;700&display=swap" rel="stylesheet">
<style>
:root{
  --navy:#0b1f5f;
  --navy-deep:#0d2266;
  --ink:#1d3578;
  --text:#5a5a5a;
  --muted:#777;
  --line:#cfcfcf;
  --footer:#dcdcdc;
  --white:#fff;
  --green:#7ab648;
}
*{margin:0;padding:0;box-sizing:border-box}
html,body{width:1200px;height:733px;overflow:hidden;background:var(--navy);font-family:"Open Sans",sans-serif;color:var(--text)}
.page{position:absolute;left:57px;top:20px;width:1085px;height:665px;background:linear-gradient(#fafafa,#fff 120px);}
.brand{position:absolute;left:11px;top:60px;display:flex;align-items:center;gap:6px}
.brand-dot{width:14px;height:14px;border-radius:50%;background:var(--navy)}
.brand-name{font-family:"Open Sans",sans-serif;font-weight:700;font-size:19px;color:var(--navy);letter-spacing:.5px}
.lang{position:absolute;right:14px;top:12px;font-size:13px;color:var(--navy)}
.nav{position:absolute;left:497px;top:56px;width:578px;height:46px;border:2px solid var(--navy);border-top:none;border-radius:0 0 8px 8px;background:linear-gradient(#fff,#f1f2f6);display:flex;align-items:center;justify-content:space-around;padding:0 10px}
.nav a{font-family:"Oswald",sans-serif;font-weight:300;font-size:18px;color:#555;text-decoration:none}
.nav a.active{color:var(--navy);font-weight:400}
.banner{position:absolute;left:10px;top:114px;width:1066px;height:263px;display:flex}
.banner div{height:100%}
.panel{position:absolute;left:11px;top:402px;width:1064px;height:200px;border:1.5px solid var(--navy-deep);border-bottom:none;border-radius:14px 14px 0 0;background:#fff}
.heading{font-family:"Oswald",sans-serif;font-weight:400;font-size:15px;line-height:22px;color:#333;letter-spacing:.3px}
.heading b{font-weight:500;color:var(--navy)}
.news{position:absolute;left:13px;top:20px;width:310px}
.more{position:absolute;right:12px;top:4px;font-size:8px;color:#555;letter-spacing:.5px;display:flex;align-items:center;gap:5px}
.more i{display:inline-block;width:8px;height:8px;border:1px solid #888;font-style:normal;font-size:7px;line-height:6px;text-align:center}
.news-box{margin-top:8px;border:1px solid var(--line);border-radius:7px;height:137px;padding:8px 0}
.news-item{display:flex;margin-bottom:6px;font-size:11.5px}
.news-date{width:80px;padding-left:8px;font-weight:700;font-size:13px;color:#666;border-right:1px dotted #999;margin-right:16px;padding-top:16px;height:40px}
.news-item h4{font-size:12px;color:#555}
.news-item p{color:#555;line-height:1.35}
.services{position:absolute;left:332px;top:20px;width:250px}
.services ul{list-style:none;margin-top:9px}
.services li{font-size:11.5px;line-height:20px;color:#555;padding-left:21px;position:relative}
.services li::before{content:"";position:absolute;left:9px;top:9px;width:3px;height:3px;background:var(--green);border-radius:50%}
.card{position:absolute;top:24px;border:1px solid var(--line);border-radius:9px;background:linear-gradient(#f2f2f2,#fff 30px);padding:8px 10px}
.download{left:606px;width:216px;height:156px}
.contact{left:834px;width:218px;height:158px}
.card p{font-size:12px;color:var(--muted);line-height:20px}
.download p{margin-top:12px;width:110px}
.contact p{margin-top:6px;padding-left:2px;line-height:18px}
.contact .call{margin-top:0}
.or{font-family:"Open Sans",sans-serif;font-weight:700;font-size:19px;line-height:24px;color:var(--navy);margin:4px 0 0}
.phone{font-size:20px;line-height:24px;color:#111;font-weight:400;margin-top:0}
.card svg{position:absolute}
.footer{position:absolute;left:0;top:599px;width:1085px;height:66px;background:var(--footer)}
.social{position:absolute;left:13px;top:13px;display:flex;gap:7px}
.social span{width:38px;height:38px;border-radius:7px;display:block}
.copy{position:absolute;right:20px;top:25px;font-size:12px;color:#444}
</style>
</head>
<body>
<div class="page">
  <div class="brand"><span class="brand-dot"></span><span class="brand-name">KELVORA®</span></div>
  <div class="lang">En | De | Es</div>
  <nav class="nav">
    <a class="active" href="#">Kelvora</a><a href="#">Dead Sea</a><a href="#">Aromatherapy</a><a href="#">Facial Care</a><a href="#">Body Care</a><a href="#">Hair Care</a><a href="#">SPAS</a>
  </nav>
  <div class="banner">
    <div style="width:147px;background:linear-gradient(#2fb3ae,#8fd0cf)" role="img" aria-label="Turquoise jar of mineral cream on salt crystals"></div>
    <div style="width:172px;background:linear-gradient(#c7906b,#a98b6c)" role="img" aria-label="Relaxed woman resting on a towel at a spa"></div>
    <div style="width:170px;background:linear-gradient(#9a8f74,#4f5a6e)" role="img" aria-label="Natural soap bar in a glass dish"></div>
    <div style="width:171px;background:linear-gradient(#efe6e0,#5a4038)" role="img" aria-label="Head massage with pink flowers"></div>
    <div style="width:406px;background:linear-gradient(120deg,#b0864f,#8a3e2a 50%,#d8c7b0)" role="img" aria-label="Purple orchid with massage stones and essential oil bottle"></div>
  </div>
  <section class="panel">
    <div class="news">
      <h2 class="heading">LATEST <b>NEWS</b></h2>
      <span class="more"><i>+</i>MORE</span>
      <div class="news-box">
        <div class="news-item"><div class="news-date">08.05 ‘11</div><div><h4>• News</h4><p>Highlights of the event &nbsp;&nbsp; Highlights of<br>the event</p></div></div>
        <div class="news-item"><div class="news-date">08.05 ‘11</div><div><h4>• News</h4><p>Highlights of the event &nbsp;&nbsp; Highlights of<br>the event</p></div></div>
      </div>
    </div>
    <div class="services">
      <h2 class="heading">OUR <b>SERVICES</b></h2>
      <ul>
        <li>some text will come here some text will come heresome text will come heresome text will come here</li>
        <li>some text will come heresome text will come heresome text will come heresome text will come here</li>
      </ul>
    </div>
    <div class="card download">
      <h2 class="heading" style="color:var(--navy)">DOWNLOAD</h2>
      <p>Click here for the Latest Product Deals for Download</p>
      <svg style="left:126px;top:42px" width="84" height="100" viewBox="0 0 84 100" aria-hidden="true">
        <path d="M10 8h22l6 8h36a4 4 0 0 1 4 4v66a4 4 0 0 1-4 4H10a4 4 0 0 1-4-4V12a4 4 0 0 1 4-4z" fill="#b9cbe0"/>
        <rect x="6" y="22" width="72" height="64" rx="4" fill="#d9e4f0"/>
        <path d="M30 36h16v22h12L38 84 18 58h12z" fill="#6cc22b" stroke="#3d8a14" stroke-width="2"/>
      </svg>
    </div>
    <div class="card contact">
      <h2 class="heading" style="color:var(--navy)">CONTACT US</h2>
      <p>Click here to send<br>us your Enquiry</p>
      <div class="or">OR</div>
      <p class="call">Call us at</p>
      <div class="phone">+11 480 215 736</div>
      <svg style="left:122px;top:46px" width="80" height="58" viewBox="0 0 80 58" aria-hidden="true">
        <path d="M4 18c0-10 72-10 72 0v6H60v-6H20v6H4z" fill="#3d8fd8"/>
        <path d="M16 24h48l6 30H10z" fill="#5aa9ea" stroke="#2d72b8" stroke-width="2"/>
        <circle cx="40" cy="38" r="11" fill="#e8f2fb" stroke="#2d72b8" stroke-width="2"/>
        <circle cx="40" cy="38" r="3" fill="#2d72b8"/>
      </svg>
    </div>
  </section>
  <footer class="footer">
    <div class="social">
      <span style="background:#3b5b9c" role="img" aria-label="Social network link"></span>
      <span style="background:#3fb5e8" role="img" aria-label="Social network link"></span>
    </div>
    <p class="copy">© 2012 Kelvora. All Rights Reserved.</p>
  </footer>
</div>
</body>
</html>
```